Envelope Design - Winner can do follow-up business

- Varnoko.com is a Swiss-based online store selling business shirts and accessories for business men
- Please visit the webpage to make yourself familiar with the company. Although the text is in German, with Plimbo translator you should be able to understand the main content.
- Our clients are mainly business men between 30 and 60 years old. Mostly with a high income working in the service industry (banking, insurance, lawyers, etc.). Sometimes there wives purchase the shirts for them ;-)
- The colors and the logo are given, as they are also used for the print materials (please see files in attachment)
- I am running several businesses and often need a talented web designer --> the winner gets substantial follow-up business
your task:
-for our company we need a new envelope design
-It should be simple and modern
-please use one of the logos in the followings.
-suprise me :)

```html
<!DOCTYPE html>
<html lang="en">
<head>
<meta charset="utf-8">
<title>Varnoko Envelope Set</title>
<link rel="stylesheet" href="https://fonts.googleapis.com/css2?family=Montserrat:wght@600&family=Open+Sans:wght@400&display=swap">
<style>
  :root {
    --backdrop: #4a2a18;
    --paper: #ffffff;
    --brand-yellow: #e8d86a;
    --brand-red: #ee3a2a;
    --ink: #1a1a1a;
    --edge: #333333;
    --faint: #f6efd9;
  }
  html, body {
    margin: 0;
    width: 1200px;
    height: 962px;
    overflow: hidden;
    background: var(--backdrop);
  }
  .envelope-set { display: block; width: 1200px; height: 962px; }
  .paper { fill: var(--paper); }
  .edge { fill: var(--paper); stroke: var(--edge); stroke-width: 1; }
  .flap-line { fill: none; stroke: var(--edge); stroke-width: 1; }
  .yellow { fill: var(--brand-yellow); }
  .red { fill: var(--brand-red); }
  .faint-mark { fill: var(--faint); }
  .wordmark {
    font-family: "Montserrat", sans-serif;
    font-weight: 600;
    letter-spacing: 2px;
  }
  .flap-name { fill: var(--brand-red); font-size: 46px; }
  .front-name { fill: var(--brand-yellow); font-size: 46px; }
  .contact {
    font-family: "Open Sans", sans-serif;
    font-size: 20px;
    fill: var(--ink);
  }
  .icon-line { fill: none; stroke: var(--brand-red); stroke-width: 1.5; }
</style>
</head>
<body>
<svg class="envelope-set" viewBox="0 0 1200 962" xmlns="http://www.w3.org/2000/svg">

  <!-- Back envelope with yellow flap -->
  <g class="envelope envelope-back">
    <rect class="paper" x="156" y="58" width="974" height="640"/>
    <path class="yellow" d="M156 58 H1130 C1120 100 1112 125 1070 138 L670 210 Q640 215 610 210 L210 138 C176 125 166 100 156 58 Z"/>
    <text class="wordmark flap-name" x="641" y="142" text-anchor="middle">VARNOKO</text>
  </g>

  <!-- Middle envelope, outlined flap -->
  <g class="envelope envelope-middle">
    <rect class="edge" x="65" y="230" width="975" height="458"/>
    <path class="flap-line" d="M65 230 C75 270 85 298 130 308 L520 380 Q545 386 575 380 L980 308 C1020 298 1030 270 1040 230"/>
    <rect class="faint-mark" x="508" y="262" width="88" height="92"/>
  </g>

  <!-- Front envelope -->
  <g class="envelope envelope-front">
    <rect class="edge" x="164" y="437" width="974" height="459"/>
    <rect class="yellow" x="164" y="713" width="974" height="183"/>
    <path class="paper" d="M185 713 H1117 V876 H780 L755 896 H545 L520 876 H185 Z"/>

    <g class="sender-name">
      <rect class="red" x="302" y="468" width="56" height="56"/>
      <text class="wordmark front-name" x="192" y="580">VARNOKO</text>
    </g>

    <g class="contact-address">
      <path class="red" d="M457 826 a9 9 0 0 1 9 9 c0 7 -9 17 -9 17 s-9 -10 -9 -17 a9 9 0 0 1 9 -9 Z M457 831 a4 4 0 1 0 0.01 0 Z" fill-rule="evenodd"/>
      <text class="contact" x="480" y="845">Street Name, City Name, State Zipcode</text>
    </g>

    <g class="contact-web">
      <circle class="icon-line" cx="564" cy="876" r="10"/>
      <ellipse class="icon-line" cx="564" cy="876" rx="4.5" ry="10"/>
      <line class="icon-line" x1="554" y1="876" x2="574" y2="876"/>
      <line class="icon-line" x1="556" y1="870" x2="572" y2="870"/>
      <line class="icon-line" x1="556" y1="882" x2="572" y2="882"/>
      <text class="contact" x="585" y="883">www.varnoko.com</text>
    </g>
  </g>
</svg>
</body>
</html>
```